Summit Bodyform Gym Website

We need a website design for our gym.

Summit is the UAE's first calisthenics and parkour gym. The theme under which the gym revolves is that one does not require any machinery to workout as our bodies could be themselves the machinery. The gym is designed to be the more of a social hub rather than an "in-and-out" gym, where people come train, have fun, hang out and socialize for a few hours rather than just train for 60 minutes then leave. The gym is designed to be a big open space with lots of natural sunlight, natural wood and plants all over the place to create a natural and refreshing setting. We also use recycled material throughout the gym and recycle our waste as being green is part of our philosophy. We currently also have some of the world's top and most recognized calisthenics athletes working with us.

We would like our website to reflect all that as well as provide a simple, interactive and fun way for visitors to be able to get class and gym information, check out gym media and contact us for bookings.

Target Market(s)

Ages 15-35

Industry/Entity Type

Fitness

Coding

Coded - Design and coding required

Number of Pages Required

4 page

Font styles to use
Decorative

Colors
0792cd

Requirements
Must have
• Class descriptions
• Gym description
• Class schedules
• Trainer profiles
• Gym philosophy
• Contact Details
Nice to have
• A link to contact us directly for a free first trial class

```html
<!DOCTYPE html>
<html lang="en">
<head>
<meta charset="utf-8">
<title>Summit Bodyform Gym</title>
<link href="https://fonts.googleapis.com/css2?family=Anton&family=Open+Sans:ital,wght@0,400;0,600;0,700;1,400&display=swap" rel="stylesheet">
<style>
:root{
  --blue:#0792cd;
  --blue-light:#bfe3f3;
  --ink:#2b2b2b;
  --text:#6b6b6b;
  --dark:#2a2627;
  --white:#ffffff;
  --line:#e3e3e3;
}
*{box-sizing:border-box;margin:0;padding:0}
html,body{width:1200px;height:3020px;overflow:hidden}
body{position:relative;font-family:"Open Sans",sans-serif;color:var(--text);background:var(--white)}
.abs{position:absolute}
.display{font-family:"Anton",sans-serif;font-weight:400;letter-spacing:.5px}

/* header */
.top-rule{left:0;top:0;width:1200px;height:4px;background:var(--blue)}
.brand{left:160px;top:22px;display:flex;align-items:center;gap:12px}
.brand-mark{width:22px;height:22px;background:var(--blue);border-radius:50%}
.brand-name{font-family:"Anton",sans-serif;font-size:40px;color:var(--ink);line-height:1}
.brand-sub{left:194px;top:68px;font-size:13px;color:var(--ink)}
.contact{top:18px;display:flex;gap:12px;align-items:center;font-size:12px;color:#555;line-height:18px}
.contact .ic{width:34px;height:34px;border:2px solid var(--blue);border-radius:50%;display:flex;align-items:center;justify-content:center;flex:none}
.nav{left:352px;top:78px;width:848px;height:52px;background:var(--blue);display:flex;align-items:center}
.nav-notch{left:316px;top:78px;width:60px;height:52px}
.nav a{font-family:"Anton",sans-serif;color:var(--white);text-decoration:none;font-size:14px;padding:0 19px;height:52px;line-height:52px;letter-spacing:.3px}
.nav a.active{background:var(--dark);padding:0 28px}

/* hero */
.hero{left:0;top:130px;width:1200px;height:520px;background:linear-gradient(180deg,#5a5a5a 0%,#3a3a3a 55%,#4a4a4a 100%)}
.hero-title{left:0;top:292px;width:1200px;text-align:center;color:var(--white);font-size:52px;line-height:70px}
.hero-sub{left:0;top:372px;width:1200px;text-align:center;color:var(--white);font-size:22px;line-height:32px}
.hero-btn{left:470px;top:448px;width:260px;height:60px;background:var(--blue);color:var(--white);display:flex;align-items:center;justify-content:center;gap:10px;font-size:21px}
.hero-arrow{top:368px;width:44px;height:44px;border:2px solid rgba(255,255,255,.6);border-radius:50%;display:flex;align-items:center;justify-content:center}

/* section headings */
.heading{left:0;width:1200px;text-align:center;font-size:24px;line-height:34px;color:var(--ink)}
.heading em{font-style:normal;color:var(--blue)}
.dots{display:flex;gap:6px}
.dots span{width:12px;height:12px;border-radius:50%;background:var(--blue)}
.lead{left:225px;width:750px;text-align:center;font-size:11px;line-height:20px}

/* cards */
.card{top:868px;width:274px;height:352px;border:1px solid var(--line);background:var(--white);text-align:center}
.card .photo{height:165px;width:100%}
.card h3{margin-top:20px;font-family:"Anton",sans-serif;font-weight:400;font-size:17px;line-height:24px;color:var(--ink)}
.card p{margin:12px auto 0;width:240px;font-size:11px;line-height:20px}
.card .btn{position:absolute;left:87px;bottom:18px;width:100px;height:40px;line-height:40px;background:var(--blue);color:var(--white);font-family:"Anton",sans-serif;font-size:14px}
.card.featured{background:var(--blue);border-color:var(--blue)}
.card.featured h3,.card.featured p{color:var(--white)}
.card.featured .btn{background:transparent;border:2px solid var(--white);line-height:36px}

/* gallery */
.gallery{left:0;top:1255px;width:1200px;height:600px;display:grid;grid-template-columns:300px 300px 300px 300px;grid-template-rows:300px 300px}
.gallery div.wide{grid-column:span 2}

/* trainers */
.trainer-band{left:0;top:1840px;width:1200px;height:460px}
.trainer-photo{left:170px;top:1832px;width:300px;height:458px;border-radius:150px 150px 0 0;background:linear-gradient(180deg,#8c6a55 0%,#2f9fd6 45%,#1f1f1f 100%)}
.trainer-copy{left:648px;top:1885px;width:440px}
.trainer-copy h2{font-size:24px;line-height:34px;color:var(--ink)}
.trainer-copy h2 em{font-style:normal;color:var(--blue)}
.trainer-copy p{font-size:11px;line-height:20px;margin-top:14px}
.btn-solid{display:block;width:100px;height:40px;line-height:40px;text-align:center;background:var(--blue);color:var(--white);font-family:"Anton",sans-serif;font-size:14px;margin-top:20px}

/* testimonial */
.avatar{left:160px;top:2476px;width:100px;height:100px;border-radius:50%;background:linear-gradient(160deg,#e7c7a4,#b88a63)}
.quote{left:290px;top:2474px;width:745px;font-size:11.5px;line-height:22px;font-style:italic}
.quote-mark{font-family:"Anton",sans-serif;font-size:22px;line-height:10px;color:var(--ink);font-style:normal;vertical-align:-4px}
.client-name{left:0;top:2590px;width:1200px;text-align:center;font-weight:700;font-size:15px;color:var(--ink)}

/* cta */
.cta{left:0;top:2660px;width:1200px;height:262px;background:var(--blue)}
.cta-title{left:0;top:2708px;width:1200px;text-align:center;color:var(--white);font-size:24px;line-height:34px}
.cta-text{left:240px;top:2760px;width:720px;text-align:center;color:var(--white);font-size:11px;line-height:20px}
.field{top:2828px;width:272px;height:48px;background:var(--white);display:flex;align-items:center;gap:8px;padding-left:16px;font-size:12px;font-style:italic;color:#777}
.signup{left:827px;top:2828px;width:108px;height:48px;background:#1f1f1f;color:var(--white);display:flex;align-items:center;justify-content:center;gap:6px;font-family:"Anton",sans-serif;font-size:14px}

/* footer */
.footer{left:0;top:2922px;width:1200px;height:98px;background:var(--dark)}
.social{left:162px;top:2962px;display:flex;gap:8px}
.social span{width:28px;height:28px;border:1.5px solid #cfcfcf;border-radius:50%}
.foot-links{right:164px;top:2948px;font-size:12px;color:#e6e6e6}
.foot-links span{margin:0 6px;color:#999}
.copyright{right:164px;top:2974px;font-size:12px;color:#e6e6e6}
</style>
</head>
<body>

<!-- header -->
<div class="abs top-rule"></div>
<div class="abs brand"><span class="brand-mark"></span><span class="brand-name">summit.</span></div>
<div class="abs brand-sub">bodyform gym</div>

<div class="abs contact" style="left:740px">
  <div class="ic"><svg width="16" height="12" viewBox="0 0 16 12"><rect x="1" y="1" width="14" height="10" fill="none" stroke="#0792cd" stroke-width="1.6"/><path d="M1 1l7 6 7-6" fill="none" stroke="#0792cd" stroke-width="1.6"/></svg></div>
  <div>Email:<br>info@summitbodyform.ae</div>
</div>
<div class="abs contact" style="left:958px">
  <div class="ic"><svg width="14" height="14" viewBox="0 0 24 24"><path d="M6.6 10.8a15 15 0 006.6 6.6l2.2-2.2a1 1 0 011-.25 11.4 11.4 0 003.6.57 1 1 0 011 1V20a1 1 0 01-1 1A17 17 0 013 4a1 1 0 011-1h3.5a1 1 0 011 1c0 1.25.2 2.45.57 3.6a1 1 0 01-.25 1z" fill="#0792cd"/></svg></div>
  <div>Phone:<br>000-000-0009</div>
</div>

<svg class="abs nav-notch" viewBox="0 0 60 52"><polygon points="0,52 36,0 60,0 60,52" fill="#2a2627"/></svg>
<nav class="abs nav">
  <a class="active">Home</a>
  <a>Class descriptions</a>
  <a>Gym description</a>
  <a>Class schedules</a>
  <a>Trainer Profiles</a>
  <a>Gym Philosophy</a>
  <a>Contact</a>
</nav>

<!-- hero -->
<div class="abs hero" role="img" aria-label="Black and white photo of an athlete training on pull-up bars inside the gym"></div>
<div class="abs hero-arrow" style="left:24px"><svg width="12" height="14" viewBox="0 0 12 14"><path d="M9 1L3 7l6 6" fill="none" stroke="#fff" stroke-width="1.6"/></svg></div>
<div class="abs hero-arrow" style="left:1132px"><svg width="12" height="14" viewBox="0 0 12 14"><path d="M3 1l6 6-6 6" fill="none" stroke="#fff" stroke-width="1.6"/></svg></div>
<h1 class="abs hero-title display">Summit Bodyform Gym</h1>
<p class="abs hero-sub display">Sed ut perspiciatis unde omnis iste natus error sit voluptatemac<br>cusunde omniantunde omnis iste nunde omnis ismque la.</p>
<div class="abs hero-btn display">
  <svg width="18" height="18" viewBox="0 0 18 18"><circle cx="9" cy="9" r="7.5" fill="none" stroke="#fff" stroke-width="1.6"/><path d="M8 5.5L11.5 9 8 12.5" fill="none" stroke="#fff" stroke-width="1.6"/></svg>
  Free First Trial Class
</div>

<!-- welcome -->
<h2 class="abs heading display" style="top:694px">Welcome to <em>Summit</em> Bodyform Gym</h2>
<div class="abs" style="left:540px;top:743px;width:120px;height:1px;background:var(--line)"></div>
<div class="abs dots" style="left:585px;top:738px"><span></span><span></span></div>
<p class="abs lead" style="top:784px">Sed ut perspiciatis unde omnis iste natus error sit voluptatem accusantium doloremque laudantium, totam remeriam, eaque ipsa quae ab illo inventore veritatis et quasi architecto beatae vitae dicta sunt explicabSed ut perspiciatis unde omnis iste natus error sit voluptatem accusantium doloremque laudantium, totam rem aperiam, eaque ipsa quae ab illo inventore veritatis et quasi architecto beatae vitae dicta sunt expli.</p>

<article class="abs card" style="left:162px">
  <div class="photo" role="img" aria-label="Athlete training with suspension straps in the gym" style="background:linear-gradient(135deg,#c9ccd0,#6f7a86)"></div>
  <h3>Calisthenics</h3>
  <p>Sed ut perspiciatis unde omnis iste natus error sit voluptatem accusantium doloremque laudantium, totam remeriam, eaque ips</p>
  <span class="btn">Read More</span>
</article>
<article class="abs card featured" style="left:462px">
  <div class="photo" role="img" aria-label="Athlete doing a street workout hold between city buildings" style="background:linear-gradient(135deg,#8fb4cf,#7a6a5c)"></div>
  <h3>Lorem ipsum</h3>
  <p>Sed ut perspiciatis unde omnis iste natus error sit voluptatem accusantium doloremque laudantium, totam remeriam, eaque ips</p>
  <span class="btn">Read More</span>
</article>
<article class="abs card" style="left:762px">
  <div class="photo" role="img" aria-label="Man training on gymnastic rings" style="background:linear-gradient(135deg,#e0e2e4,#9a8f86)"></div>
  <h3>Lorem ipsu</h3>
  <p>Sed ut perspiciatis unde omnis iste natus error sit voluptatem accusantium doloremque laudantium, totam remeriam, eaque ips</p>
  <span class="btn">Read More</span>
</article>

<!-- gallery -->
<div class="abs gallery">
  <div role="img" aria-label="Open gym floor with rigs" style="background:linear-gradient(135deg,#8a8d90,#4e5256)"></div>
  <div role="img" aria-label="Athlete doing a handstand" style="background:linear-gradient(135deg,#6c7a5c,#b4866a)"></div>
  <div role="img" aria-label="Athlete on gymnastic rings" style="background:linear-gradient(135deg,#7b7470,#3f3a37)"></div>
  <div role="img" aria-label="Dumbbell rack in front of a plant wall" style="background:linear-gradient(180deg,#6f8a3f,#2c2c2c)"></div>
  <div role="img" aria-label="Athlete hanging from rings" style="background:linear-gradient(135deg,#5d5552,#8e3a35)"></div>
  <div class="wide" role="img" aria-label="Close-up of a wooden gymnastic ring" style="background:linear-gradient(135deg,#4f6e8a,#9c8a70)"></div>
  <div role="img" aria-label="Athlete climbing wall bars" style="background:linear-gradient(135deg,#8a6a60,#6a2a2a)"></div>
</div>
<svg class="abs" style="left:0;top:1250px" width="1200" height="620" viewBox="0 0 1200 620">
  <path d="M0 0H1200V2Q600 60 0 2Z" fill="#fff"/>
  <path d="M0 620H1200V590Q600 560 0 580Z" fill="#fff"/>
</svg>

<!-- trainers -->
<svg class="abs trainer-band" viewBox="0 0 1200 460">
  <path d="M0 352L1200 306V318L0 364Z" fill="#e6eef2"/>
  <path d="M0 364L1200 318V348L0 446Z" fill="#0792cd"/>
  <path d="M0 400L420 460H0Z" fill="#bfe3f3"/>
</svg>
<div class="abs trainer-photo" role="img" aria-label="Female trainer in a blue tank top standing with hands on hips"></div>
<div class="abs trainer-copy">
  <h2 class="display"><em>Our</em> Trainers</h2>
  <div class="dots" style="margin-top:16px"><span></span><span></span></div>
  <p>Sed ut perspiciatis unde omnis iste natus error sit voluptatem accusantium doloremque laudantium, totam remeriam, eaque ipsa quae ab illo inventore veritatis et quasi architecto beatae vitae dicta sunt explicabSed ut perspiciatis unde omnis iste natus error sit voluptatem.</p>
  <p>Susantium doloremque laudantium, totam rem aperiam, eaque ipsa quae ab illo inventore veritatis et quasi architecto beatae vitae dicta sunt expli.</p>
  <span class="btn-solid">Read More</span>
</div>

<!-- testimonials -->
<h2 class="abs heading display" style="top:2386px"><em>Client</em> Testimonials</h2>
<div class="abs dots" style="left:585px;top:2430px"><span></span><span></span></div>
<div class="abs avatar" role="img" aria-label="Portrait of the client"></div>
<p class="abs quote"><span class="quote-mark">&ldquo;</span>&nbsp;&nbsp; Sed ut perspiciatis unde omnis iste natus error sit voluptatem accusantium doloremque laudantium, totam rem aperiam, eaque ipsa quae ab illo tore itatis et quasi architecto beatae vitae dicta sunt explicabo. Nemo enim ipsam voluptatem quia voluptas sit aspernatur aut odit aut fugit, sed quiaSed ut perspiciatis unde omnis iste natus error sit voluptatem accnatus error sit voluptatem accusantium doloremque lorelau dantium, totam rem aperiam, eaque ipsa qae dicta sunt eit voluptatem accnatus error sit voluptatem&nbsp;&nbsp;<span class="quote-mark">&rdquo;</span></p>
<div class="abs client-name">MARA KELLEN</div>

<!-- call to action -->
<div class="abs cta"></div>
<h2 class="abs cta-title display">Get a Free Class schedules</h2>
<p class="abs cta-text">Sed ut perspiciatis unde omnis iste natus error sit voluptatem accusantium doloremque laudantium, totam remeriam, eaque ipsa quae ab illo inventore veritatis et quasi architecto beatae vitae dicta sunt explicabSed ut perspiciatis unde omnis iste natus error sit voluptatem</p>
<div class="abs field" style="left:265px">
  <svg width="11" height="12" viewBox="0 0 11 12"><circle cx="5.5" cy="3.2" r="2.8" fill="#555"/><path d="M0 12a5.5 5 0 0111 0z" fill="#555"/></svg>Name:
</div>
<div class="abs field" style="left:546px">
  <svg width="12" height="10" viewBox="0 0 12 10"><rect width="12" height="10" fill="#555"/><path d="M0 0l6 5 6-5" fill="none" stroke="#fff" stroke-width="1"/></svg>Email:
</div>
<div class="abs signup">Sign up
  <svg width="14" height="14" viewBox="0 0 18 18"><circle cx="9" cy="9" r="7.5" fill="none" stroke="#fff" stroke-width="1.8"/><path d="M8 5.5L11.5 9 8 12.5" fill="none" stroke="#fff" stroke-width="1.8"/></svg>
</div>

<!-- footer -->
<footer class="abs footer"></footer>
<div class="abs social"><span></span><span></span><span></span><span></span><span></span></div>
<div class="abs foot-links">Home<span>|</span>Class descriptions<span>|</span>Gym description<span>|</span>Class schedules<span>|</span>Trainer profiles<span>|</span>Gym philosophy<span>|</span>Contact</div>
<div class="abs copyright">&copy; 2015 Copyright &nbsp;are reserved. Summit Terms and Conditions</div>

</body>
</html>
```